MRT Property - Business Cards

Looking for a business card & general letterhead, signage etc design for our new logo.

Colours:
000a20
0056a2
00b5ef
0088ce
68cef2

Fonts:
Poppins
Karla

Please keep look and feel of new brand - example in the zip package I sent.

```html
<!DOCTYPE html>
<html lang="en">
<head>
<meta charset="utf-8">
<title>MRT Property – Letterhead</title>
<link href="https://fonts.googleapis.com/css2?family=Poppins:wght@400;500;700&display=swap" rel="stylesheet">
<style>
  :root {
    --ink: #000a20;
    --brand-blue: #0056a2;
    --cyan: #00b5ef;
    --mid-blue: #0088ce;
    --sky: #68cef2;
    --paper: #ffffff;
    --backdrop: #626262;
  }
  * { margin: 0; padding: 0; box-sizing: border-box; }
  html, body {
    width: 1200px;
    height: 686px;
    overflow: hidden;
    background: var(--backdrop);
    font-family: "Poppins", sans-serif;
  }
  .canvas {
    position: relative;
    width: 1200px;
    height: 686px;
    display: flex;
    align-items: center;
    justify-content: center;
  }
  .letterhead {
    position: relative;
    width: 440px;
    height: 622px;
    background: var(--paper);
    padding: 38px 36px;
  }
  .letterhead__header {
    display: flex;
    justify-content: space-between;
    align-items: flex-start;
  }
  .brand {
    display: flex;
    align-items: center;
    gap: 8px;
    margin-top: 18px;
  }
  .brand__dot {
    width: 14px;
    height: 14px;
    border-radius: 50%;
    background: var(--mid-blue);
  }
  .brand__name {
    font-family: "Poppins", sans-serif;
    font-weight: 700;
    font-size: 20px;
    color: var(--brand-blue);
    letter-spacing: 0.2px;
  }
  .contact {
    display: flex;
    gap: 12px;
  }
  .contact__rule {
    width: 1.5px;
    align-self: stretch;
    background: var(--brand-blue);
  }
  .contact__body {
    font-size: 7.5px;
    line-height: 1.45;
    color: var(--ink);
  }
  .contact__address { margin-bottom: 6px; }
  .contact__line {
    display: flex;
    align-items: center;
    gap: 5px;
  }
  .contact__icon {
    width: 8px;
    height: 8px;
    flex: none;
  }
</style>
</head>
<body>
  <main class="canvas">
    <article class="letterhead">
      <header class="letterhead__header">
        <div class="brand">
          <span class="brand__dot"></span>
          <span class="brand__name">MRT Property</span>
        </div>
        <div class="contact">
          <span class="contact__rule"></span>
          <div class="contact__body">
            <p class="contact__address">Suite 4.12, Harbour Point<br>18 Meridian Lane<br>Sydney NSW 2000</p>
            <p class="contact__line">
              <svg class="contact__icon" viewBox="0 0 10 10" aria-hidden="true"><circle cx="5" cy="5" r="5" fill="var(--mid-blue)"/><path d="M3.2 2.6l1 1-.6.7a4 4 0 0 0 2.1 2.1l.7-.6 1 1-.8.8C4.8 7.3 2.7 5.2 2.4 3.4z" fill="#fff"/></svg>
              +61 2 5550 0142
            </p>
            <p class="contact__line">
              <svg class="contact__icon" viewBox="0 0 10 10" aria-hidden="true"><circle cx="5" cy="5" r="5" fill="var(--mid-blue)"/><circle cx="5" cy="5" r="2.8" fill="none" stroke="#fff" stroke-width=".7"/><path d="M2.2 5h5.6M5 2.2c-1.4 1.6-1.4 4 0 5.6M5 2.2c1.4 1.6 1.4 4 0 5.6" fill="none" stroke="#fff" stroke-width=".6"/></svg>
              www.mrtproperty.com.au
            </p>
            <p class="contact__line">
              <svg class="contact__icon" viewBox="0 0 10 10" aria-hidden="true"><circle cx="5" cy="5" r="5" fill="var(--mid-blue)"/><rect x="2.6" y="3.3" width="4.8" height="3.4" fill="none" stroke="#fff" stroke-width=".7"/><path d="M2.6 3.3L5 5.2l2.4-1.9" fill="none" stroke="#fff" stroke-width=".7"/></svg>
              info@mrtproperty.com.au
            </p>
          </div>
        </div>
      </header>
    </article>
  </main>
</body>
</html>
```